Business card design for Brivo Engineering Tandem

We need a new business card design along with all the necessary to place an order. The company is Brivo Engineering Tandem and we recently updated our logo.

```html
<!DOCTYPE html>
<html lang="en">
<head>
<meta charset="utf-8">
<title>Brivo Engineering Tandem – Business Card</title>
<link rel="stylesheet" href="https://fonts.googleapis.com/css2?family=Kanit:wght@400;500;600&display=swap">
<style>
  :root {
    --page-bg: #3a3a3c;
    --card-bg: #1f1f20;
    --brand-yellow: #e3bd24;
    --brand-grey: #a3a3a3;
    --text-light: #f2f2f2;
    --pattern-light: #bdbdbd;
    --pattern-dark: #0c0c0c;
  }
  * { margin: 0; padding: 0; box-sizing: border-box; }
  html, body { width: 1200px; height: 1059px; overflow: hidden; }
  body {
    background: var(--page-bg);
    font-family: "Kanit", sans-serif;
    position: relative;
  }
  .card {
    position: absolute;
    border-radius: 24px;
    background: var(--card-bg);
    overflow: hidden;
  }
  .card--front { left: 257px; top: 100px; width: 687px; height: 392px; }
  .card--back  { left: 253px; top: 536px; width: 694px; height: 396px; }

  .brand {
    position: absolute;
    left: 0; right: 0; top: 70px;
    display: flex; justify-content: center; align-items: center; gap: 14px;
  }
  .brand__mark { width: 18px; height: 18px; background: var(--brand-yellow); }
  .brand__name {
    font-size: 38px; font-weight: 500; color: var(--brand-grey);
    letter-spacing: 1px; text-transform: uppercase; line-height: 1;
  }

  .person {
    position: absolute; right: 387px; top: 220px; text-align: right;
  }
  .person__name {
    font-size: 32px; font-weight: 600; color: var(--brand-yellow);
    line-height: 1; text-transform: uppercase; letter-spacing: -0.3px;
  }
  .person__role {
    font-size: 17px; font-weight: 400; color: var(--text-light);
    margin-top: 8px; line-height: 1;
  }
  .divider {
    position: absolute; left: 327px; top: 216px;
    width: 2px; height: 70px; background: var(--brand-yellow);
  }
  .contacts {
    position: absolute; left: 361px; top: 211px; list-style: none;
  }
  .contacts li {
    display: flex; align-items: center; gap: 9px;
    font-size: 17px; color: var(--text-light); line-height: 27px;
  }
  .contacts svg { width: 15px; height: 15px; fill: var(--brand-yellow); flex: none; }

  .address {
    position: absolute; left: 0; right: 0; top: 338px;
    text-align: center; font-size: 17px; line-height: 24px; color: var(--text-light);
  }

  .pattern-fill {
    position: absolute; inset: 0;
    background: linear-gradient(120deg, var(--pattern-light) 0%, #6e6e6e 25%, #262626 48%, var(--pattern-dark) 70%);
  }
</style>
</head>
<body>
  <section class="card card--front">
    <div class="brand">
      <span class="brand__mark"></span>
      <span class="brand__name">Brivo Engineering Tandem</span>
    </div>

    <div class="person">
      <p class="person__name">Daniel Marsh</p>
      <p class="person__role">Managing Director</p>
    </div>

    <span class="divider"></span>

    <ul class="contacts">
      <li>
        <svg viewBox="0 0 16 16" aria-hidden="true"><path d="M1 6c0-2 3-3 7-3s7 1 7 3v1h-4V5.5H5V7H1z M3 8h10l1 6H2z"/></svg>
        01632 960418
      </li>
      <li>
        <svg viewBox="0 0 16 16" aria-hidden="true"><path d="M1 3h14v1.5L8 9 1 4.5z M1 6.5l7 4.5 7-4.5V13H1z"/></svg>
        sales@brivoengineering.co.uk
      </li>
      <li>
        <svg viewBox="0 0 16 16" aria-hidden="true"><circle cx="8" cy="8" r="7"/></svg>
        www.brivoengineering.co.uk
      </li>
    </ul>

    <p class="address">Brivo Engineering Tandem 22b Harrow Lane, Kettering NN15 4RT</p>
  </section>

  <section class="card card--back">
    <div class="pattern-fill" role="img" aria-label="Repeating brand symbol pattern fading from silver to black, with one highlighted yellow symbol"></div>
  </section>
</body>
</html>
```